Automotive component supplier needs a business card design

We need a business card design for our company called Velran Global Components Ltd based in the UK. We are a supplier of interior and exterior components to premium car manufacturers such as Corvel Ashby, Hadley Fenn, Marquist and Tavarelli. We would like to see a modern business card design that uses the colour blue.

Target Market(s)

Premium automotive car manufacturers.

Industry/Entity Type

Automotive

Contact Information for Business Card

Company Name : Velran Global Components Limited
Address: 17 Marlow Yard, Upper Heath, Warwick, CV31 8QL, United Kingdom
Web Address : www.velrancomponents-example.co.uk

Font styles to use
Other font styles liked:
• Helvetica

Colors
3176b5
0255a3
85acd3
cfdeed
cee9f5
85cae6
34a6d7
0692cd
9bcb3c

Requirements
Must have
• Clear company logo and a mixture of blue colours.
Nice to have
• A high quality modern image.
Should not have
• Multiple colours.

```html
<!DOCTYPE html>
<html lang="en">
<head>
<meta charset="utf-8">
<title>Velran Global Components – Business Card</title>
<link rel="stylesheet" href="https://fonts.googleapis.com/css2?family=Arimo:wght@400;700&display=swap">
<style>
  :root {
    --blue: #0a8fce;
    --blue-deep: #0692cd;
    --green: #9bcb3c;
    --white: #ffffff;
    --stage: #e9edf1;
    --ink-blue: #1288c9;
  }
  * { box-sizing: border-box; margin: 0; padding: 0; }
  html, body { width: 1200px; height: 900px; overflow: hidden; }
  body {
    background: var(--stage);
    font-family: "Arimo", Helvetica, Arial, sans-serif;
    display: flex;
    align-items: center;
    justify-content: center;
    gap: 40px;
  }
  .card {
    position: relative;
    width: 540px;
    height: 310px;
    overflow: hidden;
    box-shadow: 0 8px 24px rgba(0,0,0,0.15);
  }

  /* Front */
  .card--front { background: var(--blue); }
  .front-mark {
    position: absolute;
    top: 118px;
    left: 0; right: 0;
    text-align: center;
  }
  .front-mark__name {
    color: var(--white);
    font-weight: 700;
    font-size: 58px;
    letter-spacing: 2px;
    line-height: 1;
  }
  .front-stripe {
    position: absolute;
    height: 6px;
    background: var(--green);
    top: 287px;
  }
  .front-stripe--left { left: 0; width: 150px; }
  .front-stripe--right { right: 0; width: 150px; }
  .front-web {
    position: absolute;
    top: 280px;
    left: 150px; right: 150px;
    text-align: center;
    color: var(--white);
    font-size: 11.5px;
  }
  .front-web .domain { color: var(--green); }

  /* Back */
  .card--back { background: var(--white); }
  .back-rule {
    position: absolute;
    left: 0; right: 0;
    height: 3px;
    background: var(--blue-deep);
  }
  .back-rule--mid { top: 222px; }
  .back-rule--base { top: 290px; }
  .back-rule__square {
    position: absolute;
    top: -5px;
    left: 322px;
    width: 18px; height: 13px;
    background: var(--green);
    border-radius: 3px;
  }
  .identity {
    position: absolute;
    left: 28px;
    top: 70px;
    width: 215px;
  }
  .identity__company {
    color: var(--ink-blue);
    font-weight: 700;
    font-size: 21px;
    line-height: 1.1;
  }
  .identity__person {
    margin-top: 22px;
    color: var(--ink-blue);
    font-weight: 700;
    font-size: 17px;
    letter-spacing: 1.5px;
    text-align: right;
  }
  .identity__role {
    color: var(--green);
    font-size: 12px;
    text-align: right;
    margin-top: 3px;
  }
  .divider {
    position: absolute;
    left: 262px;
    top: 58px;
    width: 1px;
    height: 118px;
    background: var(--green);
  }
  .contact {
    position: absolute;
    left: 278px;
    top: 56px;
    color: var(--ink-blue);
    font-size: 12px;
    line-height: 1.35;
    list-style: none;
  }
  .contact__address { margin-bottom: 8px; }
  .contact li { display: flex; align-items: center; gap: 8px; }
  .contact svg { width: 10px; height: 10px; flex: none; }
</style>
</head>
<body>

  <section class="card card--front" aria-label="Business card front">
    <div class="front-mark">
      <span class="front-mark__name">VELRAN</span>
    </div>
    <div class="front-stripe front-stripe--left"></div>
    <div class="front-web">www.<span class="domain">velrancomponents-example</span>.co.uk</div>
    <div class="front-stripe front-stripe--right"></div>
  </section>

  <section class="card card--back" aria-label="Business card back">
    <div class="identity">
      <div class="identity__company">Velran Global Components</div>
      <div class="identity__person">DORIAN PELL</div>
      <div class="identity__role">Director</div>
    </div>

    <div class="divider"></div>

    <ul class="contact">
      <li class="contact__address">17 Marlow Yard, Upper Heath<br>Warwick, CV31 8QL, UK</li>
      <li>
        <svg viewBox="0 0 10 10" aria-hidden="true"><path d="M2 1 L4 3 L3 4.3 Q4.3 6 5.7 7 L7 6 L9 8 L7.8 9.2 Q4 8.5 0.8 2.2 Z" fill="#9bcb3c"/></svg>
        780 555-0142
      </li>
      <li>
        <svg viewBox="0 0 10 10" aria-hidden="true"><rect x="2.5" y="0.5" width="5" height="9" rx="1" fill="none" stroke="#9bcb3c" stroke-width="1.2"/><circle cx="5" cy="7.8" r="0.6" fill="#9bcb3c"/></svg>
        780 555-0198
      </li>
      <li>
        <svg viewBox="0 0 10 10" aria-hidden="true"><rect x="0.5" y="2" width="9" height="6" fill="#9bcb3c"/><path d="M0.5 2 L5 5.5 L9.5 2" fill="none" stroke="#fff" stroke-width="0.8"/></svg>
        velranparts@example.com
      </li>
      <li>
        <svg viewBox="0 0 10 10" aria-hidden="true"><circle cx="5" cy="5" r="4.3" fill="none" stroke="#9bcb3c" stroke-width="1"/><ellipse cx="5" cy="5" rx="1.8" ry="4.3" fill="none" stroke="#9bcb3c" stroke-width="0.8"/><line x1="0.7" y1="5" x2="9.3" y2="5" stroke="#9bcb3c" stroke-width="0.8"/></svg>
        www.velrancomponents-example.co.uk
      </li>
    </ul>

    <div class="back-rule back-rule--mid"><span class="back-rule__square"></span></div>
    <div class="back-rule back-rule--base"></div>
  </section>

</body>
</html>
```